Birchline Septic Solutions

Would like to see some single sided ones but would also like to see some double sided with one sided only being the logo. Owners name is Colin Vandro. Phone number is 555-214-0387
Services are pumping, inspections, installs, and repairs

Contact Information for Business Card

555-241-0387 Colin Vandro Maplewood, OH

```html
<!DOCTYPE html>
<html lang="en">
<head>
<meta charset="utf-8">
<title>Birchline Septic Solutions – Business Cards</title>
<link rel="stylesheet" href="https://fonts.googleapis.com/css2?family=Montserrat:wght@400;500;700;800&display=swap">
<style>
  :root {
    --backdrop: #4a4a4a;
    --card-black: #161616;
    --teal: #2cbdb6;
    --white: #ffffff;
    --ink-soft: #e9e9e9;
  }
  * { margin: 0; padding: 0; box-sizing: border-box; }
  html, body {
    width: 1200px; height: 801px; overflow: hidden;
    background: var(--backdrop);
    font-family: "Montserrat", sans-serif;
  }
  .sheet { position: relative; width: 1200px; height: 801px; }
  .card {
    position: absolute; top: 246px;
    width: 540px; height: 309px;
    background: var(--card-black);
    overflow: hidden;
    box-shadow: 0 14px 30px rgba(0,0,0,0.35);
  }
  .card--contact { left: 40px; }
  .card--brand { left: 620px; }

  /* contact side */
  .brand-lockup {
    position: absolute; left: 30px; top: 96px; width: 212px;
    color: var(--white); font-weight: 800; text-transform: uppercase;
    line-height: 1; white-space: nowrap;
  }
  .brand-lockup__name { font-size: 31px; letter-spacing: 0.3px; display: block; }
  .brand-lockup__tag { font-size: 11.5px; letter-spacing: 3.2px; display: block; margin-top: 9px; }

  .divider {
    position: absolute; left: 258px; top: 54px;
    width: 1.5px; height: 150px; background: var(--teal);
  }
  .contact { position: absolute; left: 282px; top: 40px; color: var(--ink-soft); }
  .contact__name { color: var(--teal); font-weight: 700; font-size: 22px; line-height: 1.05; white-space: nowrap; }
  .contact__place { font-size: 13px; margin-bottom: 18px; }
  .contact__list { list-style: none; font-size: 13px; line-height: 1.45; }
  .contact__list li { display: flex; align-items: center; gap: 7px; white-space: nowrap; }
  .contact__list svg { width: 11px; height: 11px; flex: none; fill: var(--teal); }
  .contact__address { font-size: 13px; line-height: 1.35; margin-top: 18px; }

  .edge-stripe { position: absolute; left: 0; bottom: 0; width: 540px; height: 70px; }

  /* brand side */
  .brand-hero {
    position: absolute; left: 0; right: 0; top: 64px;
    text-align: center; color: var(--white);
    font-weight: 800; text-transform: uppercase; line-height: 1;
  }
  .brand-hero__name { display: block; font-size: 58px; letter-spacing: 1px; }
  .brand-hero__tag { display: block; font-size: 19px; letter-spacing: 7px; margin-top: 12px; }
  .services-band {
    position: absolute; left: 0; right: 0; bottom: 32px; height: 24px;
    background: var(--teal); color: var(--white);
    font-size: 15px; font-weight: 500; white-space: nowrap;
    display: flex; align-items: center; justify-content: center;
  }
</style>
</head>
<body>
<main class="sheet">

  <section class="card card--contact" aria-label="Business card, contact side">
    <div class="brand-lockup">
      <span class="brand-lockup__name">Birchline</span>
      <span class="brand-lockup__tag">Septic Solutions</span>
    </div>

    <div class="divider"></div>

    <div class="contact">
      <h1 class="contact__name">Colin Vandro</h1>
      <p class="contact__place">Maplewood</p>
      <ul class="contact__list">
        <li>
          <svg viewBox="0 0 24 24" aria-hidden="true"><path d="M6.6 10.8a15.1 15.1 0 0 0 6.6 6.6l2.2-2.2a1 1 0 0 1 1-.25 11.4 11.4 0 0 0 3.6.57 1 1 0 0 1 1 1V20a1 1 0 0 1-1 1A17 17 0 0 1 3 4a1 1 0 0 1 1-1h3.5a1 1 0 0 1 1 1c0 1.25.2 2.45.57 3.57a1 1 0 0 1-.25 1z"/></svg>
          555-214-0387
        </li>
        <li>
          <svg viewBox="0 0 24 24" aria-hidden="true"><path d="M2 5h20v14H2z"/></svg>
          info@birchlineseptic.com
        </li>
        <li>
          <svg viewBox="0 0 24 24" aria-hidden="true"><circle cx="12" cy="12" r="10"/></svg>
          www.birchlineseptic.com
        </li>
      </ul>
      <p class="contact__address">Your address, City<br>State, Zip 1234</p>
    </div>

    <svg class="edge-stripe" viewBox="0 0 540 70" preserveAspectRatio="none" aria-hidden="true">
      <path d="M0 47 L278 47 L278 52 L0 52 Z" fill="var(--white)"/>
      <path d="M0 58 L300 58 C318 58 322 40 340 40 L540 40 L540 70 L0 70 Z" fill="var(--teal)"/>
    </svg>
  </section>

  <section class="card card--brand" aria-label="Business card, brand side">
    <div class="brand-hero">
      <span class="brand-hero__name">Birchline</span>
      <span class="brand-hero__tag">Septic Solutions</span>
    </div>
    <p class="services-band">Services are pumping, inspections, installs, and repairs</p>
  </section>

</main>
</body>
</html>
```